RW Framewell Inc Business cards

We need business cards using our existing logo but slightly modified. Right now the logo says RW Loadbearing Masonry. We want to keep the RW part of the design, but replace the Structural Concrete portion with "FRAMEWELL". Please see the attached file.
Ideally this would be a blank template so we can add Different Names, titles, and phone numbers later.
On the one side we want only the logo and on the other side the detail. I'm attaching an example for you to see.
Please reach out with any other questions. Our address and other details will be given out once we find a design we like.

Target Market(s)

Construction Industry

```html
<!DOCTYPE html>
<html lang="en">
<head>
<meta charset="utf-8">
<title>RW Framewell Inc – Business Cards</title>
<link rel="stylesheet" href="https://fonts.googleapis.com/css2?family=Oswald:wght@400;500&family=Open+Sans:wght@400&display=swap">
<style>
  :root {
    --backdrop: #e2e2e2;
    --card-white: #ffffff;
    --brand-blue: #1d78c1;
    --ink-grey: #8a8b8d;
    --rule-grey: #a9aaac;
    --text-dark: #555658;
    --silver: #c7cacd;
  }
  * { margin: 0; padding: 0; box-sizing: border-box; }
  html, body {
    width: 1200px; height: 900px; overflow: hidden;
    background: var(--backdrop);
  }
  .sheet {
    width: 1200px; height: 900px;
    display: flex; flex-direction: column;
    align-items: center; justify-content: center; gap: 60px;
  }
  .card {
    width: 630px; height: 360px;
    border-radius: 28px;
    box-shadow: 0 6px 18px rgba(0,0,0,0.18);
    position: relative;
  }
  .card-front {
    background: var(--card-white);
    display: flex; align-items: center;
  }
  .brand {
    width: 315px;
    display: flex; flex-direction: column; align-items: center;
    font-family: "Oswald", sans-serif; font-weight: 500;
    color: var(--brand-blue);
    line-height: 1;
  }
  .brand-initials { font-size: 112px; letter-spacing: 2px; }
  .brand-name { font-size: 22px; letter-spacing: 14px; margin-top: 10px; padding-left: 14px; }
  .divider {
    width: 1px; height: 210px; background: var(--rule-grey);
  }
  .details { padding-left: 36px; }
  .person-name {
    font-family: "Oswald", sans-serif; font-weight: 500;
    font-size: 40px; color: var(--ink-grey); line-height: 1; letter-spacing: 0.5px;
  }
  .job-title {
    font-family: "Oswald", sans-serif; font-weight: 500;
    font-size: 22px; color: var(--brand-blue); margin-top: 4px; letter-spacing: 0.5px;
  }
  .contact-list { list-style: none; margin-top: 24px; }
  .contact-item {
    display: flex; align-items: center; gap: 10px;
    font-family: "Open Sans", sans-serif; font-size: 19px; color: var(--text-dark);
    margin-bottom: 10px;
  }
  .contact-icon { width: 18px; height: 18px; fill: var(--brand-blue); flex: none; }
  .card-back {
    background: var(--brand-blue);
    display: flex; align-items: center; justify-content: center;
  }
  .card-back .brand { width: auto; color: var(--silver); }
  .card-back .brand-initials { font-size: 150px; }
  .card-back .brand-name { font-size: 26px; letter-spacing: 18px; padding-left: 18px; }
</style>
</head>
<body>
<main class="sheet">
  <section class="card card-front" aria-label="Card front with contact details">
    <div class="brand">
      <span class="brand-initials">RW</span>
      <span class="brand-name">FRAMEWELL</span>
    </div>
    <div class="divider"></div>
    <div class="details">
      <p class="person-name">YOUR NAME</p>
      <p class="job-title">JOB TITLE</p>
      <ul class="contact-list">
        <li class="contact-item">
          <svg class="contact-icon" viewBox="0 0 24 24" aria-hidden="true"><path d="M6.6 10.8a15.1 15.1 0 0 0 6.6 6.6l2.2-2.2c.3-.3.7-.4 1-.2 1.1.4 2.3.6 3.6.6.6 0 1 .4 1 1V20c0 .6-.4 1-1 1A17 17 0 0 1 3 4c0-.6.4-1 1-1h3.5c.6 0 1 .4 1 1 0 1.3.2 2.5.6 3.6.1.3 0 .7-.2 1z"/></svg>
          <span>000 000 0000</span>
        </li>
        <li class="contact-item">
          <svg class="contact-icon" viewBox="0 0 24 24" aria-hidden="true"><path d="M2 5h20v14H2z M2 5l10 8 10-8" fill="var(--brand-blue)"/><path d="M2 5l10 8 10-8" fill="none" stroke="#fff" stroke-width="1.6"/></svg>
          <span>youremail@xyz.com</span>
        </li>
      </ul>
    </div>
  </section>

  <section class="card card-back" aria-label="Card back with brand name">
    <div class="brand">
      <span class="brand-initials">RW</span>
      <span class="brand-name">FRAMEWELL</span>
    </div>
  </section>
</main>
</body>
</html>
```